Bram Keystone Homes needs a business card

We need a business card for a new company in Canada, Ontario. Our company is all about luxury contraction homes for our clients. Our product and services are custom projects design. Under the business logo that will be created, we want a slogan that will be a memorable phrase for consumers to remember us to tell their friends and relatives.

Additional infomation
- Ludovic Entrasse
- President / Ceo
-519.604.3087

Find point what luxury construction products and services can be done

We like to see colors:
- #663300
- and something other colors or color that would attract the client needs and wants

The final design should communicate leads from new or old clients that will grow our empire. Most of all, we try to work among the budget that clients want

NOTE
- we also need an icon for the business (Example: Instagram, Facebook, and Whatsapp icons)
- We want the company name to be remembered easily for clients and our distributors who would get our orders.
- we need an icon on the business cards: Facebook and Instagram.

Thanks,
Bram Keystone Homes

```html
<!DOCTYPE html>
<html lang="en">
<head>
<meta charset="utf-8">
<title>Bram Keystone Homes – Business Card</title>
<link rel="stylesheet" href="https://fonts.googleapis.com/css2?family=Work+Sans:wght@400;600;800&display=swap">
<style>
  :root {
    --backdrop: #1f1f1f;
    --card-brown: #663300;
    --card-brown-dark: #5e3214;
    --card-brown-light: #6e4222;
    --ink-light: #ffffff;
    --rule: rgba(255, 255, 255, 0.55);
  }
  * { margin: 0; padding: 0; box-sizing: border-box; }
  html, body {
    width: 1200px;
    height: 900px;
    overflow: hidden;
    background: var(--backdrop);
    font-family: "Work Sans", Arial, sans-serif;
    color: var(--ink-light);
  }
  .stage {
    width: 1200px;
    height: 900px;
    display: flex;
    flex-direction: column;
    align-items: center;
    justify-content: center;
    gap: 40px;
  }
  .card {
    width: 700px;
    height: 400px;
    position: relative;
    background: linear-gradient(135deg, var(--card-brown-dark) 0%, var(--card-brown) 55%, var(--card-brown-light) 100%);
    box-shadow: 0 10px 24px rgba(0, 0, 0, 0.5);
  }
  .brand-name {
    font-weight: 800;
    letter-spacing: 0.5px;
    line-height: 1;
    white-space: nowrap;
  }
  .brand-tagline {
    font-weight: 600;
    text-transform: uppercase;
    letter-spacing: 0.6px;
    white-space: nowrap;
  }

  /* Front */
  .card-front {
    display: flex;
    flex-direction: column;
    align-items: center;
    justify-content: center;
  }
  .card-front .brand-name { font-size: 40px; }
  .card-front .brand-tagline { font-size: 14.5px; margin-top: 8px; }

  /* Back */
  .card-back .brand-lockup {
    position: absolute;
    top: 58px;
    right: 40px;
    text-align: left;
  }
  .card-back .brand-name { font-size: 29px; }
  .card-back .brand-tagline { font-size: 10.5px; margin-top: 6px; }

  .person {
    position: absolute;
    left: 48px;
    top: 208px;
  }
  .person-name { font-size: 24px; font-weight: 600; }
  .person-title { font-size: 17px; font-weight: 400; letter-spacing: 0.6px; margin-top: 2px; }

  .divider {
    position: absolute;
    left: 48px;
    right: 40px;
    top: 282px;
    height: 1px;
    background: var(--rule);
  }
  .contact {
    position: absolute;
    left: 48px;
    top: 300px;
    font-size: 16.5px;
    font-weight: 400;
    letter-spacing: 0.4px;
    line-height: 1.6;
  }
  .contact-line { white-space: nowrap; }
</style>
</head>
<body>
  <main class="stage">
    <section class="card card-front" aria-label="Business card front">
      <div class="brand-name">Bram Keystone Homes</div>
      <div class="brand-tagline">- Home Renovations - Custom Project Design -</div>
    </section>

    <section class="card card-back" aria-label="Business card back">
      <div class="brand-lockup">
        <div class="brand-name">Bram Keystone Homes</div>
        <div class="brand-tagline">- Home Renovations - Custom Project Design -</div>
      </div>

      <div class="person">
        <div class="person-name">Ludovic Entrasse</div>
        <div class="person-title">President / Ceo</div>
      </div>

      <div class="divider"></div>

      <div class="contact">
        <div class="contact-line">P : 519.604.3087 | E : info@bramkeystone.com | W : www.bramkeystone.com</div>
        <div class="contact-line">A : 1187 Harrow Lane Stratford, ON N5A 2K9</div>
      </div>
    </section>
  </main>
</body>
</html>
```